Brenwick Coaching Website

I would like someone to design my website. I have an existing site which is really basic and needs an overhaul. I have attached a powerpoint with all the information I require. I am flexible with the design and layout and am ok with graphics being added to enhance the attractiveness of the site.

```html
<!DOCTYPE html>
<html lang="en">
<head>
<meta charset="utf-8">
<title>Brenwick Coaching</title>
<link rel="stylesheet" href="https://fonts.googleapis.com/css2?family=Open+Sans:wght@400;600&family=Roboto:wght@400&display=swap">
<style>
:root{
  --blue:#1f73c0;
  --blue-light:#3f9fe8;
  --blue-dark:#1e72bd;
  --orange:#f07a1a;
  --orange-light:#f9c89c;
  --orange-text:#ec5a1c;
  --white:#ffffff;
  --footer-top:#3a3a3a;
  --footer-bottom:#0d0d0d;
  --hero-sky:#f3c860;
  --hero-field:#7fae2c;
}
*{box-sizing:border-box;margin:0;padding:0}
html,body{width:1200px;height:1101px;overflow:hidden;background:var(--white)}
body{position:relative;font-family:"Open Sans",sans-serif}
.site-header{position:absolute;left:0;top:0;width:1200px;height:133px}
.brand{position:absolute;left:171px;top:46px;display:flex;align-items:center;gap:10px;font-size:30px;font-weight:400;color:var(--blue)}
.brand-dot{width:18px;height:18px;background:var(--orange-text)}
.contact{position:absolute;right:169px;top:52px;text-align:right;font-size:17px;line-height:27px}
.contact .phone{color:var(--orange-text)}
.contact .email{color:var(--blue)}
.hero{position:absolute;left:0;top:133px;width:1200px;height:413px;
  background:linear-gradient(180deg,#e9c77a 0%,var(--hero-sky) 45%,#f6dc9a 62%,#9ab43a 75%,var(--hero-field) 100%)}
.hero-title{position:absolute;left:326px;top:176px;font-size:51px;font-weight:600;color:var(--blue);letter-spacing:-0.3px;white-space:nowrap}
.tile{position:absolute;left:171px;width:313px;height:71px;
  background:linear-gradient(180deg,var(--orange-light) 0%,#f7a458 50%,var(--orange) 100%);
  color:var(--white);font-size:22px;font-weight:600;padding-left:29px;display:flex;align-items:center}
.welcome{position:absolute;left:492px;top:582px;width:538px;height:232px;
  background:linear-gradient(180deg,var(--blue-light) 0%,var(--blue-dark) 100%);color:var(--white)}
.welcome h1{position:absolute;left:15px;top:19px;font-size:20px;font-weight:600}
.welcome .copy{position:absolute;left:17px;top:54px;width:358px;font-size:16.6px;line-height:23.5px;text-align:justify}
.welcome .copy p+p{margin-top:4px}
.portrait{position:absolute;left:391px;top:60px;width:128px;height:124px;background:linear-gradient(160deg,#8a7f6c,#3f3428)}
.cta{position:absolute;left:493px;top:823px;width:538px;height:71px;
  background:linear-gradient(180deg,var(--blue-light) 0%,var(--blue-dark) 100%);
  color:var(--white);font-size:18px;font-weight:600;display:flex;align-items:center;padding-left:19px}
.site-footer{position:absolute;left:0;top:944px;width:1200px;height:157px;
  background:linear-gradient(180deg,var(--footer-top),var(--footer-bottom));color:var(--white);font-family:"Roboto",sans-serif}
.footer-links{position:absolute;left:0;width:1200px;top:30px;text-align:center;font-size:11px}
.copyright{position:absolute;left:183px;top:96px;font-size:10.5px}
.social{position:absolute;left:482px;top:81px;display:flex;gap:6px}
.social span{width:34px;height:34px;border-radius:50%;background:#e8e8e8;border:2px solid #555}
.newsletter{position:absolute;left:819px;top:86px;width:207px;height:24px;background:var(--white);display:flex;align-items:center;justify-content:space-between;padding:0 6px}
.newsletter span{font-size:10px;color:#555}
</style>
</head>
<body>
<header class="site-header">
  <div class="brand"><span class="brand-dot"></span>Brenwick Coaching</div>
  <div class="contact">
    <div class="phone">1300 555 019</div>
    <div class="email">jordan.hale@brenwickcoaching.com</div>
  </div>
</header>

<section class="hero" role="img" aria-label="Sunset over rolling green hills and meadows">
  <div class="hero-title">Brenwick Coaching</div>
</section>

<nav>
  <a class="tile" style="top:582px">Individual Coaching (1)</a>
  <a class="tile" style="top:662px">Group Work (2)</a>
  <a class="tile" style="top:743px">Resources (3)</a>
  <a class="tile" style="top:823px">Inspiration Booth (5)</a>
</nav>

<section class="welcome">
  <h1>WELCOME TO BRWK COACHING</h1>
  <div class="copy">
    <p>Welcome to Brenwick Coaching where we put a new perspective on the way you work, live and play.</p>
    <p>Through our programs you will learn new skills &amp; techniques to enable you to break through the barriers that have kept you from reaching your full potential up to now.</p>
  </div>
  <div class="portrait" role="img" aria-label="Portrait photo of the coach"></div>
</section>

<a class="cta">Get your free 30 minute introductory coaching session... (4)</a>

<footer class="site-footer">
  <div class="footer-links">Terms of Service | Returns | Policy Privacy | Event | Contact | Blog | Sitemap</div>
  <div class="copyright">Copy Right © 2014. All rights reserved.</div>
  <div class="social" aria-label="Social media links">
    <span></span><span></span><span></span><span></span><span></span><span></span>
  </div>
  <div class="newsletter">
    <span>News Letter</span>
    <svg width="28" height="18" viewBox="0 0 28 18" aria-hidden="true">
      <rect x="1" y="1" width="26" height="16" fill="none" stroke="#333" stroke-width="2"/>
      <path d="M1 1 L14 11 L27 1" fill="none" stroke="#333" stroke-width="2"/>
    </svg>
  </div>
</footer>
</body>
</html>
```